Bold Harbor Web Design Layout (no HTML)

We require the layout only for a website.  No html or logo is required - just the layout.

A refreshed and revitalized website to coincide with the relaunch of our brand. We are looking for a clean simplistic design that is easy to use and presents relevant information effectively.
We are an events management company specializing in conferences.
Updates

Thank you for your design. We really like the imagery. Essentially we are after a home page design (one page) that incorporates the 3 main buttons (request a proposal, select a venue and specials) while providing the relevant information on our service via functionality similar to that on www.plivtrak.com ie using the large arrow to scroll over the relevant topic to receive information. We hope to finalise the contest in the next week and hope to consider your revised entry.

Thanks!

Target Market(s)

Australian corporate sector primarily Managing Directors or their assistants. Any business looking to hold a conference for up 500 delegates however we are primarily targeting the decision maker so need to ensure we are communicating on their terms.

Industry/Entity Type

Event

Requirements
Must have
• Incorporate the elements from the attached document however with complete creative license as to their layout. Our main competitors are gathorly.com.au, talkhollowhq.com.au both sites are bland and not user friendly.
Nice to have
• Colours red, silver and black. Note we are running a separate contest to refresh our logo.
• We like the functionality of plivtrak.com

```html
<!DOCTYPE html>
<html lang="en">
<head>
<meta charset="utf-8">
<title>Bold Harbor – Conference Events</title>
<link href="https://fonts.googleapis.com/css2?family=Questrial&family=Arimo:wght@400;700&display=swap" rel="stylesheet">
<style>
:root{
  --red:#c4161c;
  --red-dark:#8f1218;
  --charcoal:#3a3a3c;
  --black:#000;
  --silver:#c2c2c2;
  --panel:#e8e8e8;
  --bg:#c4c4c4;
  --ink:#111;
  --grey-text:#5a5a5a;
  --white:#fff;
}
*{margin:0;padding:0;box-sizing:border-box}
html,body{width:1200px;height:725px;overflow:hidden}
body{position:relative;background:var(--bg);font-family:"Questrial",sans-serif;color:var(--ink)}
.backdrop-top{position:absolute;left:0;top:0;width:1200px;height:103px;background:linear-gradient(#000 0%,#1a1a1a 20%,#8a8a8a 100%)}
.backdrop-band{position:absolute;left:0;top:103px;width:1200px;height:41px;background:#ececec}
.page{position:absolute;left:157px;top:15px;width:882px;height:622px;background:var(--white);border-radius:8px;box-shadow:0 2px 6px rgba(0,0,0,.25)}
.header{position:absolute;left:166px;top:23px;width:865px;height:80px;background:var(--silver);border-radius:7px 7px 0 0}
.logo{position:absolute;left:38px;top:42px;font-size:11px;color:#222}
.search{position:absolute;left:587px;top:47px;display:flex;align-items:center}
.search-label{font-family:"Arimo",sans-serif;font-weight:700;font-size:13px;margin-right:2px}
.search-field{width:178px;height:20px;background:var(--white);border:1px solid #ddd}
.search-go{margin-left:2px;width:27px;height:26px;border-radius:3px;background:linear-gradient(#e0353a,#a90f14);border:1px solid #7a0b0f;color:var(--white);font-family:"Arimo",sans-serif;font-weight:700;font-size:12px;display:flex;align-items:center;justify-content:center}
.nav{position:absolute;left:166px;top:103px;width:865px;height:41px;background:var(--charcoal)}
.nav-home-icon{position:absolute;left:37px;top:18px}
.nav ul{list-style:none;position:absolute;left:70px;top:19px;display:flex;gap:11px}
.nav li{font-size:13px;line-height:16px;color:var(--white);white-space:nowrap;letter-spacing:-.2px}
.nav li.active{color:#e8eef6;font-weight:700;margin-right:2px}
.nav-marker{position:absolute;left:354px;top:139px;width:0;height:0;border-left:6px solid transparent;border-right:6px solid transparent;border-bottom:5px solid var(--white)}
.hero{position:absolute;left:185px;top:158px;width:630px;height:170px;background:var(--panel)}
.art{display:block;position:absolute}
.hero-figure{left:15px;top:7px;width:65px;height:163px;background:linear-gradient(#777,#bbb 80%,#e0e0e0)}
.hero-copy{position:absolute;left:133px;top:57px;width:452px;font-size:14px;line-height:16px}
.hero-goal{position:absolute;left:133px;top:129px;font-size:14px;font-weight:700}
.hero-copy b{font-weight:700}
.benefits{position:absolute;left:183px;top:333px;width:632px;height:34px;background:linear-gradient(90deg,var(--red),var(--red-dark))}
.benefits span{position:absolute;top:6px;font-size:14px;color:var(--white);white-space:nowrap}
.benefits-marker{position:absolute;left:53px;top:28px;border-left:7px solid transparent;border-right:7px solid transparent;border-bottom:6px solid var(--white)}
.offer-title{position:absolute;left:196px;top:378px;font-size:14.5px;font-weight:700;color:var(--grey-text);white-space:nowrap}
.offer-list{position:absolute;left:343px;top:404px;list-style:none;font-size:14px;line-height:15.8px;color:var(--grey-text)}
.offer-list li::before{content:"•";position:absolute;left:-13px;font-size:11px}
.offer-list li{position:relative}
.offer-art{left:207px;top:438px;width:88px;height:122px;border-radius:10px;background:radial-gradient(ellipse at 50% 45%,#e62a24,#a3121a 70%)}
.offer-note{position:absolute;left:328px;top:530px;width:386px;font-size:14px;line-height:16px;color:var(--grey-text)}
.learn-more{display:inline-block;margin-left:6px;padding:1px 8px;border-radius:7px;background:var(--red);color:var(--white);font-size:7px;vertical-align:2px}
.play{position:absolute;left:770px;top:555px}
.side-card{position:absolute;left:822px;width:218px}
.side-tab{position:absolute;left:0;top:0;width:120px;height:17px;background:var(--red);color:var(--white);font-size:12px;padding:1px 0 0 6px;border-radius:0 2px 0 0;white-space:nowrap}
.side-text{position:absolute;left:2px;top:20px;width:102px;font-size:11px;line-height:12.4px}
.side-art{left:116px;top:9px;width:82px;height:85px;border-radius:8px;background:radial-gradient(circle,#f0473c,#c4161c 70%)}
.side-art.clock{background:radial-gradient(circle,#fff 55%,#e6e6e6 62%,#c4161c 66%,#fff 72%);border-radius:50%}
.side-divider{position:absolute;left:822px;width:210px;height:2px;background:linear-gradient(90deg,transparent,#d0d0d0 20%,#d0d0d0 80%,transparent)}
.footer{position:absolute;left:166px;top:605px;width:865px;height:23px;background:var(--black);color:var(--white);font-family:"Arimo",sans-serif;font-size:9.5px;text-align:center;line-height:23px}
</style>
</head>
<body>
<div class="backdrop-top"></div>
<div class="backdrop-band"></div>
<div class="page"></div>

<header class="header">
  <div class="logo">BOLD HARBOR</div>
  <form class="search">
    <span class="search-label">SEARCH:</span>
    <span class="search-field"></span>
    <span class="search-go">GO</span>
  </form>
</header>

<nav class="nav">
  <svg class="nav-home-icon" width="19" height="15" viewBox="0 0 19 15"><path d="M9.5 0 19 8h-3v7h-4.5v-4h-4v4H3V8H0z" fill="#fff"/></svg>
  <ul>
    <li class="active">HOME</li>
    <li>SERVICES</li>
    <li>VENUES</li>
    <li>CLIENTS</li>
    <li>REGISTER</li>
    <li>CONTACT US</li>
  </ul>
</nav>
<span class="nav-marker" style="left:250px"></span>

<section class="hero">
  <div class="art hero-figure" role="img" aria-label="Illustration of a businessman in a grey suit with a red tie"></div>
  <p class="hero-copy"><b>Bold Harbor</b>’ professional conference team specialises in solutions. We work closely with a core group of clients to ensure desired outcomes, on time and in budget.</p>
  <p class="hero-goal">Our goal is to make sure your conference is:</p>
</section>

<div class="benefits">
  <span style="left:16px">Cost Effective</span>
  <span style="left:126px">Expertely Managed &amp; Hassle Free</span>
  <span style="left:361px">Outcome Focussed</span>
  <span style="left:519px">Well Attended</span>
  <i class="benefits-marker"></i>
</div>

<h2 class="offer-title">We offer a complete range of finance&nbsp; packages including;</h2>
<div class="art offer-art" role="img" aria-label="Illustration of a large red 3D dollar sign"></div>
<ul class="offer-list">
  <li>total conference underwriting</li>
  <li>online delegate payment gateway</li>
  <li>substantially discounted rooming rates</li>
  <li>no upfront costs</li>
  <li>zero management fees</li>
  <li>free venue sourcing</li>
  <li>free delegate booking management</li>
</ul>
<p class="offer-note">Minimise your costs and free your cash flow to focus on your core business functions. We’ll ensure maximum return from your conference budget. <span class="learn-more">LEARN MORE</span></p>
<svg class="play" width="32" height="32" viewBox="0 0 32 32"><circle cx="16" cy="16" r="14.5" fill="#f2f2f2" stroke="#999" stroke-width="1.5"/><path d="M12 9.5 23 16 12 22.5z" fill="#fff" stroke="#aaa"/></svg>

<aside>
  <div class="side-card" style="top:156px">
    <div class="side-tab">Browse Conference</div>
    <p class="side-text">Not sure where to start? We have over 60 properties to choose from both domestically and international.</p>
    <div class="art side-art" style="left:115px;top:10px;width:83px;height:85px" role="img" aria-label="Red glossy map of Australia"></div>
  </div>
  <div class="side-divider" style="top:259px"></div>
  <div class="side-card" style="top:276px">
    <div class="side-tab">Request Proposal</div>
    <p class="side-text">Not sure where to start? We have over 60 properties to choose from both domestically and international.</p>
    <div class="art side-art clock" style="left:133px;top:19px;width:78px;height:78px" role="img" aria-label="Red-rimmed wall clock"></div>
  </div>
  <div class="side-divider" style="top:379px"></div>
  <div class="side-card" style="top:400px">
    <div class="side-tab">Special Offers</div>
    <p class="side-text">Not sure where to start? We have over 60 properties to choose from both domestically and international.</p>
    <div class="art side-art" style="left:120px;top:19px;width:76px;height:76px;border-radius:50%" role="img" aria-label="Red starburst badge with a dollar sign"></div>
  </div>
</aside>

<footer class="footer">Ph: 1300 555 014. P.O. Box 4417, Harbourview NSW 2090. Bold Harbor. All Rights Reserved. 2009</footer>
</body>
</html>
```